Redesign Fitness Photos for Facebook Ads Needed

We are a fun, energetic, group fitness facility that needs to have a few (3) photos doctored up and turned into ads for Facebook & Instagram.
I would like the photos to be doctored up so that they are clear, bright, energetic.  Feel free to manipulate the photos, backgrounds, cropping, cutting as needed.
I would like to include text on photos:
Pulsora
New Year
Challenge
* Fitness Training  * Nutritional Support * Motivation & Support
Join Now
The text should be roughly the size of the examples included in order to comply with facebooks text size requirements
I have included 3 examples of another gyms ads which I like how the images are eye catching and text is clearly visible and pops with color.
Although I have attached multiple images that can be used,  I am only looking for 3 completed designs to be used for ads.

You choose the images that you feel you can modify the best.
I look forward to seeing your design.
Thank you.

```html
<!DOCTYPE html>
<html lang="en">
<head>
<meta charset="UTF-8">
<title>Pulsora Challenge Ad</title>
<link href="https://fonts.googleapis.com/css2?family=Archivo+Black&family=Montserrat:wght@500;700&display=swap" rel="stylesheet">
<style>
  :root {
    --sky-blue: #1d95d3;
    --lilac: #8a6fb5;
    --hot-pink: #c24a9e;
    --deep-violet: #6a51a5;
    --ink-violet: #2e1f5c;
    --magenta: #b8239a;
    --lemon: #efe412;
    --black: #111111;
    --white: #ffffff;
    --panel: rgba(236, 214, 240, 0.5);
  }
  * { margin: 0; padding: 0; box-sizing: border-box; }
  html, body {
    width: 1200px;
    height: 628px;
    overflow: hidden;
    background: var(--deep-violet);
  }
  .ad {
    position: relative;
    width: 1200px;
    height: 628px;
    overflow: hidden;
    font-family: "Archivo Black", "Arial Black", sans-serif;
  }
  .ad__art {
    position: absolute;
    inset: 0;
    width: 1200px;
    height: 628px;
  }
  .brand {
    position: absolute;
    left: 500px;
    top: 86px;
    width: 220px;
    text-align: center;
    color: var(--white);
  }
  .brand__name {
    font-family: "Archivo Black", "Arial Black", sans-serif;
    font-size: 40px;
    line-height: 1;
  }
  .brand__tagline {
    margin-top: 5px;
    font-family: "Montserrat", Arial, sans-serif;
    font-weight: 500;
    font-size: 9.5px;
    letter-spacing: 2.6px;
  }
  .benefits {
    position: absolute;
    right: 54px;
    top: 0;
    list-style: none;
    text-align: right;
    color: var(--ink-violet);
    font-size: 29.5px;
    letter-spacing: 1.2px;
  }
  .benefits li {
    position: absolute;
    right: 0;
    white-space: nowrap;
    line-height: 1;
  }
  .benefits li:nth-child(1) { top: 141px; }
  .benefits li:nth-child(2) { top: 231px; }
  .benefits li:nth-child(3) { top: 316px; }
  .headline {
    position: absolute;
    left: 384px;
    top: 437px;
    font-size: 91px;
    line-height: 1;
    letter-spacing: -1px;
    color: var(--ink-violet);
    text-shadow: 14px 8px 0 var(--white);
  }
  .cta {
    position: absolute;
    left: 700px;
    top: 540px;
    font-size: 36px;
    line-height: 1;
    letter-spacing: 1px;
    color: var(--white);
  }
</style>
</head>
<body>
<main class="ad">
  <svg class="ad__art" viewBox="0 0 1200 628" xmlns="http://www.w3.org/2000/svg">
    <defs>
      <linearGradient id="sky" x1="0" y1="0" x2="1" y2="0.55">
        <stop offset="0" stop-color="var(--sky-blue)"/>
        <stop offset="0.45" stop-color="var(--lilac)"/>
        <stop offset="1" stop-color="var(--hot-pink)"/>
      </linearGradient>
      <linearGradient id="athlete-tones" x1="0" y1="0" x2="0" y2="1">
        <stop offset="0" stop-color="#b89a8c"/>
        <stop offset="0.35" stop-color="#3a3440"/>
        <stop offset="0.7" stop-color="#55586a"/>
        <stop offset="1" stop-color="#d8d8e0"/>
      </linearGradient>
    </defs>

    <rect class="backdrop" width="1200" height="628" fill="url(#sky)"/>

    <path class="wave" d="M0 509 C120 490 230 440 300 330 C330 285 350 252 370 252 C430 252 520 330 580 370 C620 395 660 410 700 410 C780 410 830 370 900 300 L1166 82 L1200 60 L1200 628 L0 628 Z"
          fill="var(--deep-violet)" stroke="var(--white)" stroke-width="1"/>

    <g class="rings" fill="none" stroke="var(--magenta)" stroke-width="4">
      <circle cx="761" cy="547" r="218"/>
      <circle cx="782" cy="559" r="192"/>
    </g>

    <path class="dash dash--lemon" d="M330 130 C380 80 430 55 490 48 L1172 45"
          fill="none" stroke="var(--lemon)" stroke-width="17" stroke-dasharray="44 45"/>
    <path class="dash dash--magenta" d="M0 392 C40 330 55 220 95 130 C120 70 165 20 215 0"
          fill="none" stroke="var(--magenta)" stroke-width="13" stroke-dasharray="40 40"/>
    <path class="dash dash--magenta" d="M240 600 C280 500 300 380 340 300 C380 230 440 180 540 172 L955 170"
          fill="none" stroke="var(--magenta)" stroke-width="13" stroke-dasharray="42 44"/>
    <path class="dash dash--black" d="M85 622 C130 560 160 470 200 380 C230 310 250 250 265 180"
          fill="none" stroke="var(--black)" stroke-width="11" stroke-dasharray="40 60"/>

    <g class="panels" fill="var(--panel)">
      <polygon points="845,125 1176,125 1176,192 785,192"/>
      <polygon points="763,209 1171,209 1171,276 706,276"/>
      <polygon points="684,294 1171,294 1171,360 626,360"/>
    </g>

    <rect class="athlete" role="img" aria-label="Photo of a woman in a deep squat pressing a dumbbell overhead, on a light striped backdrop"
          x="72" y="48" width="232" height="556" rx="18"
          fill="url(#athlete-tones)"/>
  </svg>

  <header class="brand">
    <div class="brand__name">Pulsora</div>
    <div class="brand__tagline">Personal Group Training</div>
  </header>

  <ul class="benefits">
    <li>Fitness Training</li>
    <li>Nutritional Support</li>
    <li>Motivation &amp; Support</li>
  </ul>

  <h1 class="headline">CHALLENGE</h1>
  <p class="cta">JOIN NOW</p>
</main>
</body>
</html>
```